Lotstallmart.com Webpage Design

Design Brief for lotstallmart.com (Copy of Brief also in attached Word file)

Name of Website- lotstallmart.com (existing logo and look & feel of website to be changed)

Logo - Finalised. The logo files are attached with the brief as “logo.jpeg”. The “Blue- Grey” version of the logo is for use on lighter backgrounds and the “Orange-White” version of the logo is for use on darker backgrounds. (A full Black version of the logo is also attached). Both versions may be used in different parts of the website. All attached files are in .png format.
Status - The website in functional and is undergoing user trials. However, we want to improve the look & feel of the website so at it seems
a. cotemporary,
b. Easy to Navigate
c. professional and
d. Vibrant.

Please visit ‘lotstallmart.com’ to check out the website and its functionalities – please use it only as a reference for the features & functions to be provided, however the designer should use a ‘Free Hand’ in designing the composition of various parts of the webpage without getting too influenced by the existing design

Objective of the Website ‘lotstallmart.com –
a. It is a portal focussed on listing of ‘Retail’ specific real-estate properties by developers, owners and realty brokers. The properties shall listed under the following four categories-
i. Retail Malls
ii. Shopping Complexes
iii. High-street shops
iv. Retail Warehouses
*refer lotstallmart.com for better clarity

b. The abovementioned properties shall be listed either for ‘Sale’ or ‘rent\lease’ or both

c. Users shall visit the site in case they wish to acquire a retail \ shop space either on ‘sale’ or ‘rent’. These Users would be able to specify the ‘Search Criteria’ through the tool-bars provided on the website – the ‘Search Criteria’ shall comprise of ‘Type of space category’, ‘City’, ‘Locality’, transaction type ie ‘Rent \ Sale’ and ‘Area Range’

d. The main revenue model for the website shall be listing fee ( or advertising charges ) payable by those listing their properties on the website.

Three Main Pages of Website (lotstallmart.com) that need to be designed -
a. Main Home Page (visit the web link - http://lotstallmart.com/ ) - The main home page has the “Search Toolbar” for specifying of Search Criteria by the User. It shall also have the following features & functions-
i. Main Advertising Banner
ii. Featured Projects
iii. New Launches
iv. Toolbar with buttons – ‘Advertise with Us’, ‘Listings Alert’, ‘Mart Wizards’, ‘Advertiser Login’

b. Property Listings Page (visit the web link - http://lotstallmart.com/gurgaon-in-india ) - The List of property options that match the Criteria specified by the ‘User’ get displayed on this page.

c. Property Detail Page - When the ‘User’ clicks on the “More….” Button on the ‘Property Listings Page’ (given in point b. above) the web page with the details of the property opens. (For Example – visit the web link - http://lotstallmart.com/vorne-Shopping-Complex-vorne-quadrion-gurgaon-636 )

Note:- Please refer to attached ‘Shopping’ related images the designer may use them on the website to provide a look & feel of retail if required – either separately or rotate in a single window

Target Market(s)

Retailers & Investors looking for retail space, Real Estate Brokers, Developers

Industry/Entity Type

Advertising

Number of Pages Required

3 page

Requirements
Must have
• Refer to existing site lotstallmart.com -- all the existing functionalities are a must have.
Nice to have
• The Designer may use the retail related images on the website if required for making it more vibrant. Refer attached images Shopping(1-6).jpg

```html
<!DOCTYPE html>
<html lang="en">
<head>
<meta charset="utf-8">
<title>Lotstallmart.com – Retail Space Listings</title>
<link href="https://fonts.googleapis.com/css2?family=Open+Sans:wght@400;600;700;800&display=swap" rel="stylesheet">
<style>
:root{
  --navy:#1f2a36;
  --navy-deep:#161e27;
  --blue:#1a8fd1;
  --blue-dark:#0f5f95;
  --orange:#f08a1c;
  --sky:#d6ecf8;
  --page:#f3f4f5;
  --ink:#333b44;
  --muted:#7a838c;
  --line:#d4d9de;
  --white:#ffffff;
}
*{box-sizing:border-box;margin:0;padding:0}
html,body{width:1200px;height:2896px;overflow:hidden}
body{font-family:"Open Sans",Arial,sans-serif;color:var(--ink);background:var(--page);font-size:13px}
.wrap{width:1080px;margin:0 auto;position:relative}

/* top city bar */
.city-bar{height:44px;background:var(--navy-deep);color:#b9c4ce;font-size:12px;line-height:44px;text-align:center;border-bottom:1px solid #2c3845}
.city-bar span{margin:0 6px}

/* header */
.site-header{height:136px;background:var(--navy);color:var(--white)}
.site-header .wrap{height:136px;display:flex;align-items:center}
.brand{display:flex;align-items:center;gap:12px;width:300px}
.brand-dot{width:34px;height:34px;border-radius:50%;background:var(--orange)}
.brand-name{font-size:30px;font-weight:700;color:var(--orange)}
.main-nav{display:flex;gap:44px;flex:1;padding-left:30px}
.main-nav a{color:var(--blue);font-weight:600;font-size:15px;text-decoration:none;line-height:1.3}
.main-nav small{display:block;color:#9aa7b3;font-size:11px;font-weight:400}
.header-cta{text-align:center;width:200px}
.header-cta p{font-size:12px;color:#d6dde3;margin-bottom:6px}
.btn-login{display:inline-block;background:var(--orange);color:var(--white);font-weight:700;font-size:12px;padding:8px 16px;border-radius:3px}
.header-cta small{display:block;font-size:11px;color:var(--blue);margin-top:6px}

/* hero */
.hero{height:460px;padding-top:40px}
.hero .wrap{display:flex;gap:20px}
.banner{width:720px;height:400px;position:relative;background:linear-gradient(135deg,#d9b08a,#a6634a 55%,#5a3a33);border-radius:3px;overflow:hidden}
.banner-caption{position:absolute;left:0;bottom:0;right:0;background:rgba(20,26,34,.78);padding:14px 20px}
.banner-caption h2{color:var(--orange);font-size:20px;font-weight:700}
.banner-caption p{color:#d8dde2;font-size:12px;margin-top:4px}
.search-panel{width:340px;height:400px;background:var(--white);border:1px solid var(--line);border-radius:3px}
.search-panel h3{background:var(--blue);color:var(--white);font-size:16px;padding:10px 14px;display:flex;align-items:center;gap:8px}
.search-body{padding:12px 14px}
.checks{display:grid;grid-template-columns:1fr 1fr;gap:6px 8px;font-size:11px;margin-bottom:10px}
.checks label{display:flex;align-items:center;gap:5px}
.box{width:10px;height:10px;border:1px solid #9aa3ab;background:var(--white);flex:none}
.field-label{font-size:11px;font-weight:600;margin:8px 0 4px}
.field{height:26px;border:1px solid var(--line);border-radius:2px;font-size:11px;color:var(--muted);line-height:24px;padding:0 8px;display:flex;justify-content:space-between}
.btn-search{display:block;margin:16px auto 0;width:110px;text-align:center;background:var(--blue);color:var(--white);font-weight:700;font-size:14px;padding:7px 0;border-radius:3px}

/* categories */
.categories{height:220px;background:var(--white);border-top:1px solid var(--line);border-bottom:1px solid var(--line)}
.categories .wrap{display:flex;justify-content:space-around;padding-top:30px}
.cat{text-align:center;width:220px}
.cat-icon{width:100px;height:100px;border-radius:50%;border:3px solid var(--blue);margin:0 auto 12px;display:flex;align-items:center;justify-content:center;background:var(--white)}
.cat h4{color:var(--blue-dark);font-size:17px;font-weight:700}
.cat p{font-size:12px;color:var(--muted)}

/* listing sections */
.listings{padding-top:40px}
.listings.featured{height:520px}
.listings.launches{height:500px;background:var(--white)}
.section-title{font-size:28px;font-weight:700;color:var(--blue);margin-bottom:22px}
.section-title small{font-size:13px;color:var(--muted);font-weight:400;margin-left:8px}
.cards{display:grid;grid-template-columns:repeat(4,1fr);gap:24px}
.card-photo{height:160px;border-radius:2px;position:relative}
.card-tag{position:absolute;left:0;bottom:10px;background:var(--orange);color:var(--white);font-size:10px;font-weight:700;padding:3px 8px}
.card-meta{display:flex;gap:14px;font-size:11px;color:var(--muted);padding:8px 0;border-bottom:1px solid var(--line)}
.card-meta span{display:flex;align-items:center;gap:4px}
.card h5{font-size:18px;font-weight:700;color:var(--blue-dark);margin:10px 0 6px;white-space:nowrap}
.card p{font-size:11.5px;color:var(--muted);line-height:1.5}
.card .view{display:block;font-size:11px;font-weight:700;color:var(--orange);margin-top:8px}
.launches .card-meta{border-bottom:none}

/* info band */
.info-band{height:560px;background:var(--sky);padding-top:40px}
.info-band .wrap{display:grid;grid-template-columns:250px 250px 260px 260px;gap:20px}
.info-band h4{font-size:16px;font-weight:700;color:var(--blue-dark);margin-bottom:12px}
.alert-card{background:var(--white);border:1px solid #b7d6ea;padding:14px;border-radius:3px}
.alert-card .intro{display:flex;gap:10px;font-size:11px;color:var(--muted);margin-bottom:14px}
.alert-card .field{margin-bottom:10px}
.alert-card .opt{display:flex;align-items:center;gap:6px;font-size:11px;margin-top:6px}
.editor-photo{height:180px;background:linear-gradient(160deg,#c7a88a,#7b5b48);border-radius:2px}
.info-band p{font-size:11.5px;line-height:1.6;color:#4c5660}
.btn-more{display:inline-block;margin-top:14px;background:var(--orange);color:var(--white);font-size:12px;font-weight:700;padding:6px 18px;border-radius:3px}
.wizards{background:var(--blue-dark);color:var(--white);padding:18px;border-radius:3px;height:480px}
.wizards h4{color:var(--white)}
.wizards p{color:#cfe3f1;margin-bottom:14px}
.wizards .field{background:var(--white);margin-bottom:10px}
.wizards .area{height:80px}
.btn-send{display:block;width:80px;margin-left:auto;background:var(--orange);text-align:center;font-size:12px;font-weight:700;padding:6px 0;border-radius:3px}

/* footer */
.site-footer{height:420px;background:var(--navy);color:#c4cdd6;padding-top:40px}
.site-footer .wrap{display:grid;grid-template-columns:200px 170px 380px 1fr;gap:36px}
.site-footer h4{color:var(--white);font-size:17px;font-weight:700;margin-bottom:14px;white-space:nowrap}
.site-footer ul{list-style:none;font-size:12px;line-height:1.9}
.site-footer li::before{content:"›";color:var(--orange);margin-right:6px}
.site-footer p{font-size:12px;line-height:1.7}
.socials{display:flex;gap:6px;margin-top:12px}
.socials span{width:20px;height:20px;border-radius:3px;background:#3d4b59}
.footer-brand{position:absolute;right:0;top:270px;display:flex;align-items:center;gap:8px}
.footer-brand .brand-dot{width:24px;height:24px}
.footer-brand b{color:var(--orange);font-size:20px;font-weight:700}
.copyright{height:36px;background:var(--navy-deep);color:#8a96a2;font-size:11px;line-height:36px}
</style>
</head>
<body>

<div class="city-bar">
  <span>Bangalore</span>|<span>Chennai</span>|<span>Greater Noida</span>|<span>Gurgaon</span>|<span>Hyderabad</span>|<span>Jaipur</span>|<span>Kharna</span>|<span>Kolkata</span>|<span>Mumbai</span>|<span>Noida</span>|<span>Pune</span>|<span>Surat</span>
</div>

<header class="site-header">
  <div class="wrap">
    <div class="brand"><span class="brand-dot"></span><span class="brand-name">lotstallmart</span></div>
    <nav class="main-nav">
      <a href="#">Advertise with us<small>Standard listing 1999</small></a>
      <a href="#">Mart Wizards<small>Shop Search Services</small></a>
      <a href="#">Listing Alert</a>
    </nav>
    <div class="header-cta">
      <p>List Your Property Here</p>
      <span class="btn-login">ADVERTISER LOGIN</span>
      <small>New Member? Register</small>
    </div>
  </div>
</header>

<section class="hero">
  <div class="wrap">
    <div class="banner" role="img" aria-label="Photo of shoppers with shopping bags in a retail mall">
      <div class="banner-caption">
        <h2>Verana Promenade Gurgaon</h2>
        <p>Lorem ipsum dolor sit amet, consectetuer adipiscing elit, sed diam nonummy nibh euismod tincidunt ut laoreet dolore magna.</p>
      </div>
    </div>
    <aside class="search-panel">
      <h3><svg width="16" height="16" viewBox="0 0 16 16"><circle cx="6.5" cy="6.5" r="5" fill="none" stroke="#fff" stroke-width="2"/><path d="M10 10l5 5" stroke="#fff" stroke-width="2"/></svg>Property Search</h3>
      <div class="search-body">
        <div class="checks">
          <label><span class="box"></span>Retail Malls</label>
          <label><span class="box"></span>Shopping Complex</label>
          <label><span class="box"></span>High street Shops</label>
          <label><span class="box"></span>Retail Warehouse</label>
        </div>
        <div class="field-label">Sale Or Rent Or Both:</div>
        <div class="field">Sale Or Rent Or Both<span>▾</span></div>
        <div class="field-label">Select City:</div>
        <div class="field">Select City<span>▾</span></div>
        <div class="field-label">Select Locality/Micro Market:</div>
        <div class="field">Select Locality<span>▾</span></div>
        <div class="field-label">Enter Keywords:</div>
        <div class="field">Name of Project, Developer etc</div>
        <span class="btn-search">Search</span>
      </div>
    </aside>
  </div>
</section>

<section class="categories">
  <div class="wrap">
    <div class="cat">
      <div class="cat-icon"><svg width="54" height="54" viewBox="0 0 54 54"><path d="M6 48V22L27 8l21 14v26z" fill="#1f2a36"/><rect x="14" y="28" width="8" height="8" fill="#fff"/><rect x="32" y="28" width="8" height="8" fill="#fff"/><rect x="23" y="36" width="8" height="12" fill="#fff"/></svg></div>
      <h4>Retail Malls</h4><p>Centrally Air Conditioned</p>
    </div>
    <div class="cat">
      <div class="cat-icon"><svg width="54" height="54" viewBox="0 0 54 54"><path d="M4 10h8l6 24h26l5-18H15" fill="none" stroke="#1f2a36" stroke-width="4" stroke-linejoin="round"/><circle cx="21" cy="42" r="4" fill="#1f2a36"/><circle cx="40" cy="42" r="4" fill="#1f2a36"/></svg></div>
      <h4>Shopping Complex</h4><p>Non Air-Conditioned Building</p>
    </div>
    <div class="cat">
      <div class="cat-icon"><svg width="54" height="54" viewBox="0 0 54 54"><rect x="6" y="30" width="12" height="18" fill="#1f2a36"/><rect x="21" y="12" width="12" height="36" fill="#1f2a36"/><rect x="36" y="22" width="12" height="26" fill="#1f2a36"/></svg></div>
      <h4>High Street Shops</h4><p>Road Facing Retail</p>
    </div>
    <div class="cat">
      <div class="cat-icon"><svg width="54" height="54" viewBox="0 0 54 54"><path d="M4 20L27 8l23 12v28H4z" fill="#1f2a36"/><rect x="12" y="26" width="30" height="22" fill="#fff"/><path d="M12 32h30M12 38h30M12 44h30" stroke="#1f2a36" stroke-width="2"/></svg></div>
      <h4>Retail warehouses</h4><p>Back-end Retail Storage</p>
    </div>
  </div>
</section>

<section class="listings featured">
  <div class="wrap">
    <h2 class="section-title">Featured Retail Projects <small>Across India</small></h2>
    <div class="cards">
      <article class="card">
        <div class="card-photo" role="img" aria-label="Photo of a mall atrium interior" style="background:linear-gradient(160deg,#d8c7b0,#8a7460)"><span class="card-tag">GURGAON</span></div>
        <div class="card-meta"><span>▣ 1200 sq</span><span>⌂ 4 Beds</span><span>◫ 3 Baths</span></div>
        <h5>Corvin Atrium</h5>
        <p>Lorem ipsum dolor sit amet, consec tetuer adipiscing elit sed diam nonummy nibh euismod tincidunt ut laoreet dolore magna aliquam erat volutpat.</p>
        <span class="view">VIEW THE LISTINGS</span>
      </article>
      <article class="card">
        <div class="card-photo" role="img" aria-label="Photo of a shopping complex exterior" style="background:linear-gradient(160deg,#9fb9cf,#54708a)"><span class="card-tag">SOHNA</span></div>
        <div class="card-meta"><span>▣ 1200 sq</span><span>⌂ 4 Beds</span><span>◫ 3 Baths</span></div>
        <h5>Pelora Square Sohna</h5>
        <p>Lorem ipsum dolor sit amet, consec tetuer adipiscing elit sed diam nonummy nibh euismod tincidunt ut laoreet dolore magna aliquam erat volutpat.</p>
        <span class="view">VIEW THE LISTINGS</span>
      </article>
      <article class="card">
        <div class="card-photo" role="img" aria-label="Photo of a lit mall facade at dusk" style="background:linear-gradient(160deg,#6f7f9a,#2f3950)"><span class="card-tag">NOIDA</span></div>
        <div class="card-meta"><span>▣ 1200 sq</span><span>⌂ 4 Beds</span><span>◫ 3 Baths</span></div>
        <h5>The Grand Bazaar Place</h5>
        <p>Lorem ipsum dolor sit amet, consec tetuer adipiscing elit sed diam nonummy nibh euismod tincidunt ut laoreet dolore magna aliquam erat volutpat.</p>
        <span class="view">VIEW THE LISTINGS</span>
      </article>
      <article class="card">
        <div class="card-photo" role="img" aria-label="Photo of a mall building and forecourt" style="background:linear-gradient(160deg,#b7c9d8,#7c8f9c)"><span class="card-tag">DELHI</span></div>
        <div class="card-meta"><span>▣ 1200 sq</span><span>⌂ 4 Beds</span><span>◫ 3 Baths</span></div>
        <h5>Linden Mall</h5>
        <p>Lorem ipsum dolor sit amet, consec tetuer adipiscing elit sed diam nonummy nibh euismod tincidunt ut laoreet dolore magna aliquam erat volutpat.</p>
        <span class="view">VIEW THE LISTINGS</span>
      </article>
    </div>
  </div>
</section>

<section class="listings launches">
  <div class="wrap">
    <h2 class="section-title">Featured New Launches <small>Across India</small></h2>
    <div class="cards">
      <article class="card">
        <div class="card-photo" role="img" aria-label="Photo of a glass retail tower" style="background:linear-gradient(160deg,#a9c4dc,#4f6f8f)"><span class="card-tag">BHOPAL</span></div>
        <div class="card-meta"><span>▣ 1200 sq</span><span>⌂ 4 Beds</span><span>◫ 3 Baths</span></div>
        <h5>Kestrel Arcade 91</h5>
        <p>Lorem ipsum dolor sit amet, consec tetuer adipiscing elit sed diam nonummy nibh euismod tincidunt ut laoreet dolore magna aliquam erat volutpat.</p>
        <span class="view">VIEW THE LISTINGS</span>
      </article>
      <article class="card">
        <div class="card-photo" role="img" aria-label="Photo of a modern retail building" style="background:linear-gradient(160deg,#cbd6df,#8697a5)"><span class="card-tag">DELHI</span></div>
        <div class="card-meta"><span>▣ 1200 sq</span><span>⌂ 4 Beds</span><span>◫ 3 Baths</span></div>
        <h5>Quill Metropolis</h5>
        <p>Lorem ipsum dolor sit amet, consec tetuer adipiscing elit sed diam nonummy nibh euismod tincidunt ut laoreet dolore magna aliquam erat volutpat.</p>
        <span class="view">VIEW THE LISTINGS</span>
      </article>
      <article class="card">
        <div class="card-photo" role="img" aria-label="Photo of a mall entrance" style="background:linear-gradient(160deg,#d3c0a7,#8d7458)"><span class="card-tag">PUNE</span></div>
        <div class="card-meta"><span>▣ 1200 sq</span><span>⌂ 4 Beds</span><span>◫ 3 Baths</span></div>
        <h5>Astra Mall</h5>
        <p>Lorem ipsum dolor sit amet, consec tetuer adipiscing elit sed diam nonummy nibh euismod tincidunt ut laoreet dolore magna aliquam erat volutpat.</p>
        <span class="view">VIEW THE LISTINGS</span>
      </article>
      <article class="card">
        <div class="card-photo" role="img" aria-label="Photo of a commercial centre against blue sky" style="background:linear-gradient(160deg,#8fbbe0,#3f6a93)"><span class="card-tag">AGRA</span></div>
        <div class="card-meta"><span>▣ 1200 sq</span><span>⌂ 4 Beds</span><span>◫ 3 Baths</span></div>
        <h5>Kestrel Skyline Plaza</h5>
        <p>Lorem ipsum dolor sit amet, consec tetuer adipiscing elit sed diam nonummy nibh euismod tincidunt ut laoreet dolore magna aliquam erat volutpat.</p>
        <span class="view">VIEW THE LISTINGS</span>
      </article>
    </div>
  </div>
</section>

<section class="info-band">
  <div class="wrap">
    <div>
      <h4>Listing Alert</h4>
      <div class="alert-card">
        <div class="intro">
          <svg width="30" height="22" viewBox="0 0 30 22"><rect x="1" y="1" width="28" height="20" fill="none" stroke="#f08a1c" stroke-width="2"/><path d="M1 1l14 11L29 1" fill="none" stroke="#f08a1c" stroke-width="2"/></svg>
          <span>Subscribe For Fortnightly Email Update on New Listings @ Lotstallmart</span>
        </div>
        <div class="field">Enter email address</div>
        <div class="field">Select options<span>▾</span></div>
        <div class="field">Select area<span>▾</span></div>
        <div class="opt"><span class="box"></span>select total format of interest</div>
        <div class="opt"><span class="box"></span>select city of interest</div>
      </div>
    </div>
    <div>
      <h4>Editors choice</h4>
      <div class="editor-photo" role="img" aria-label="Photo of a featured retail project"></div>
      <p style="margin-top:12px">Lorem ipsum dolor sit amet, consectetuer adipiscing elit, sed diam nonummy nibh euismod tincidunt ut laoreet dolore magna aliquam erat volutpat.</p>
      <span class="btn-more">More...</span>
    </div>
    <div>
      <h4>Who We Are</h4>
      <p>Lotstallmart.com is a Specialised Web based platform for Retail Space, featuring properties across India under various formats such as Retail Malls, Shopping Complexes, High-street Shops and Retail Warehouses, which provide the logistic back end for the retail business. Lotstallmart.com is useful to various category of users as follows: a. Developers, b. Owners, c. Brokers and d. Retailers and Investors seeking space.</p>
      <span class="btn-more">More...</span>
    </div>
    <div class="wizards">
      <h4>Mart Wizards</h4>
      <p>Post your Retail Space requirement with us and our experts shall get back with suitable options and even help you in your transaction. This is a Free Service!</p>
      <div class="field">Enter your email address</div>
      <div class="field">Mobile</div>
      <div class="field area">Add Description of Requirement</div>
      <span class="btn-send">SEND</span>
    </div>
  </div>
</section>

<footer class="site-footer">
  <div class="wrap">
    <div>
      <h4>About Stallrow Central</h4>
      <ul><li>About Us</li><li>Privacy Policy</li><li>Terms of Use</li><li>Contact Us</li><li>Site Map</li></ul>
    </div>
    <div>
      <h4>&nbsp;</h4>
      <ul><li>Retail Malls</li><li>Shopping Complex</li><li>High Street Shops</li><li>Retail Warehouses</li></ul>
    </div>
    <div>
      <h4>Who We Are</h4>
      <p>Lotstallmart.com - About Us<br>Lotstallmart.com is a Specialised Web based platform for Retail Space, featuring properties across India under various formats such as Retail Malls, Shopping Complexes, High-Street Shops and Retail Warehouses which provide the logistic back end for the retail business.</p>
    </div>
    <div>
      <h4>Contact Us</h4>
      <p>Stallrow Central<br>Unit No. 000, 4th Floor,<br>Lorem Ipsum Building,<br>Sector-x, Gurgaon - 122002<br><br>Phone : 000-000-0000<br>Fax : 000 - 000 - 0000</p>
      <div class="socials"><span></span><span></span><span></span><span></span></div>
    </div>
    <div class="footer-brand"><span class="brand-dot"></span><b>lotstallmart</b></div>
  </div>
</footer>
<div class="copyright"><div class="wrap">Copyright © 2013 Stallrow Central.com. All rights reserved.</div></div>

</body>
</html>
```